We need UI/UX design for a public, informational website for The Copper Lantern.
The pages, structure, and content scope are already defined. Designers are required to work only on the UI/UX layout of these existing pages, focusing on clarity, hierarchy, spacing, and usability. Do not add, remove, rename, or reinterpret pages or content.
The website is strictly informational only. It must not include accounts, onboarding, payments, custody, escrow administration, marketplaces, dashboards, or any transactional functionality.
Scope of work
Apply UI/UX design to the predefined website pages
Design layout for text, images, notices, and sections
Ensure consistent components and layout patterns across page types
Optimize layouts for long form, compliance focused content
Content writing, page creation, and branding changes are out of scope.
Structure reference
The complete page list, hierarchy, and content definitions are provided in the technical documentation and must be treated as the primary source of truth.
A Figma link is provided only as a light visual reference for page existence and structure:
https://meadow-knot-48203956.plumsite.example/
Designers must rely on the documentation for in depth and authoritative reference.
Brand guidelines
The Copper Lantern has existing brand guidelines and official logos, including light and dark versions. These assets will be provided and must be followed exactly. Designers must not redesign, alter, or reinterpret the brand identity.
Look and feel direction
The desired visual direction is inspired by:
https://ledgerwaltz.example/
This reference is provided only to indicate:
Institutional and enterprise tone
Clean, modern typography
Strong hierarchy and generous whitespace
Editorial, content first layouts
Do not copy branding, layouts, components, or assets from the reference site.
Hero section direction
The hero section should follow a similar structural approach to the hero used on https://ledgerwaltz.example/
, meaning:
Strong editorial framing
Clear headline hierarchy
Calm, institutional first impression
However, the background video must be Abu Dhabi focused, not generic or global. The video should visually reflect:
Abu Dhabi skyline or architectural language
Institutional, sovereign, long term infrastructure tone
Clean, slow, cinematic motion
No promotional, marketing, or lifestyle visuals
The hero must remain informational, restrained, and credible. No hype. No calls to invest. No implied participation.
Constraints
One global primary CTA only: “Continue to Halvemark” (external)
All other interactions must be informational
No visuals or language implying offers, investment, eligibility, or participation
Clear separation between informational content and any external operational platforms
Deliverables
High fidelity UI/UX designs created in Figma, covering:
Desktop layouts
Tablet layouts where relevant
Mobile layouts
Complete Figma file(s) including:
All designed pages defined in the technical documentation
A reusable component library (headers, footers, cards, notice panels, forms, CTAs, typography styles, spacing system)
Clearly defined layout grids, spacing rules, and text styles
Proper use of components and variants, not detached frames
Designs prepared for developer handoff, including:
Clear layer naming and structure
Auto layout where appropriate
Consistent use of styles and components
Responsive behavior demonstrated within Figma
Notes or annotations only where necessary for clarity
No prototypes, interactions, or motion design beyond basic layout states, unless explicitly requested. The focus is static UI/UX clarity, not animation.
A detailed technical specification document and official brand assets will be provided.
Any designs delivered outside Figma, that alter structure or content, or that ignore the defined constraints, boundaries, or tone will be rejected.

```html
<!DOCTYPE html>
<html lang="en">
<head>
<meta charset="utf-8">
<title>The Copper Lantern</title>
<link href="https://fonts.googleapis.com/css2?family=Outfit:wght@300;400;500;600;700&display=swap" rel="stylesheet">
<style>
:root{
  --ink:#111111;
  --white:#ffffff;
  --black:#000000;
  --mist:#eeeef0;
  --card:#3b3b3b;
  --accent:#4aa9f4;
  --violet:#a88ce6;
  --muted:#bdbdbd;
}
*{margin:0;padding:0;box-sizing:border-box}
html,body{width:1200px;height:4728px;overflow:hidden}
body{position:relative;font-family:"Outfit",sans-serif;color:var(--ink);background:var(--white)}
.abs{position:absolute}
.photo{position:absolute}
h1,h2,h3{font-weight:600;letter-spacing:-0.2px}
.section-title{font-size:35px;line-height:1.3;font-weight:600}
.body-text{font-size:11.5px;line-height:1.62;font-weight:400}
.btn{position:absolute;background:var(--accent);color:var(--white);font-size:11px;display:flex;align-items:center;justify-content:center;border-radius:2px;text-decoration:none}

/* hero */
.hero{position:absolute;left:0;top:0;width:1200px;height:793px;background:linear-gradient(180deg,#6e5a4a 0%,#86705c 35%,#8e7058 58%,#6e4b33 75%,#5a3a25 100%);overflow:hidden}
.hero .photo{inset:0;background:linear-gradient(180deg,rgba(60,45,38,.35) 0%,rgba(0,0,0,0) 40%,rgba(40,20,10,.25) 100%)}
.brand{position:absolute;display:flex;align-items:center;gap:10px;color:var(--white);font-weight:400;letter-spacing:.5px}
.brand .dot{border:2px solid var(--white);border-radius:50%}
.nav{position:absolute;left:560px;top:40px;width:550px;height:43px;border:1px solid rgba(255,255,255,.45);border-radius:5px;display:flex;align-items:center;justify-content:space-around;padding:0 14px;font-size:11.5px;color:var(--white)}
.nav span.dd::after{content:"";display:inline-block;width:4px;height:4px;border-right:1px solid #fff;border-bottom:1px solid #fff;transform:rotate(45deg);margin-left:6px;position:relative;top:-3px}
.hero-title{position:absolute;left:90px;top:300px;font-size:50px;font-weight:600;color:var(--white)}
.hero-lede{position:absolute;left:90px;top:382px;width:570px;font-size:11px;line-height:1.72;font-weight:600;color:var(--white)}
.hero-link{position:absolute;left:90px;top:480px;font-size:11px;font-weight:600;color:var(--white)}
.notice{position:absolute;left:796px;top:602px;width:404px;height:191px;background:rgba(70,48,34,.55);color:var(--white);padding:45px 40px 0 61px}
.notice h3{font-size:13px;font-weight:600;margin-bottom:12px}
.notice p{font-size:10px;line-height:1.55;font-weight:300}

/* ecosystem */
.eco-card{position:absolute;top:2228px;width:230px;height:225px;background:var(--card);color:var(--white);text-align:center;padding:80px 22px 0}
.eco-card h3{font-size:14px;font-weight:600;margin-bottom:10px}
.eco-card p{font-size:8.5px;line-height:1.55;color:var(--muted)}

/* footer */
.footer{position:absolute;left:0;top:4244px;width:1200px;height:484px;background:var(--black);color:var(--white)}
.f-col{position:absolute;top:142px}
.f-col h4{font-size:13px;font-weight:600;margin-bottom:12px}
.f-col li{list-style:none;font-size:11px;line-height:21px;color:#d6d6d6}
.f-rule{position:absolute;left:70px;top:399px;width:1080px;height:1px;background:#2c2c2c}
.copy{position:absolute;left:0;top:428px;width:1200px;text-align:center;font-size:10px;color:#d0d0d0}
</style>
</head>
<body>

<!-- Hero -->
<section class="hero">
  <div class="photo" role="img" aria-label="City skyline with a tall tower rising above desert dunes at dusk, warm sepia tones"></div>
  <div class="brand" style="left:92px;top:44px;font-size:20px"><span class="dot" style="width:28px;height:28px"></span>THE COPPER LANTERN</div>
  <nav class="nav">
    <span>Home</span><span class="dd">Framework</span><span class="dd">Projects</span><span class="dd">Halvemark</span><span class="dd">Insights</span><span class="dd">Company</span><span class="dd">Contact</span>
  </nav>
  <h1 class="hero-title">The Copper Lantern</h1>
  <p class="hero-lede">Is a governance and project origination group. Its purpose is to define structural standards and oversight principles for complex initiatives that may involve multiple parties, staged execution, and long-term accountability. This website publishes those standards and explains how responsibilities are separated across governance, operations, and project-level execution.</p>
  <div class="hero-link">Continue to Halvemark &nbsp;→</div>
  <aside class="notice">
    <h3>This site is informational.</h3>
    <p>It does not provide onboarding, account access, eligibility checks, custody of funds, escrow administration, or transaction execution. Where operational workflows exist, they are provided through the Halvemark operating platform under separate terms and policies.</p>
  </aside>
</section>

<!-- Governance -->
<section>
  <div class="photo" style="left:141px;top:906px;width:375px;height:202px;background:linear-gradient(160deg,#2a5e99,#8fb3d4 55%,#cfd9e2)" role="img" aria-label="Curved glass towers against a blue sky"></div>
  <div class="photo" style="left:90px;top:1125px;width:229px;height:174px;background:linear-gradient(180deg,#9fb7c9,#5d7b8e 55%,#3d5c3e)" role="img" aria-label="City skyline across a green mangrove coast"></div>
  <div class="photo" style="left:338px;top:1125px;width:222px;height:218px;background:linear-gradient(160deg,#8fa8bd,#3e6474 50%,#7a4c3b)" role="img" aria-label="Cluster of curved glass office towers"></div>
  <h2 class="section-title abs" style="left:638px;top:1016px;width:400px">Governance and Project Origination</h2>
  <p class="body-text abs" style="left:638px;top:1117px;width:400px">Governance in this context refers to the standards that determine how projects are structured and how oversight is described. Origination refers to the initial design and definition of an initiative, including role separation, reporting expectations, and boundary setting before execution begins. The Copper Lantern focuses on these governance-level elements rather than on operating day-to-day workflows.</p>
</section>

<!-- Clear role separation -->
<section>
  <div class="abs" style="left:0;top:1459px;width:620px;height:449px;background:var(--mist)"></div>
  <h2 class="section-title abs" style="left:110px;top:1584px">Clear Role Separation</h2>
  <p class="body-text abs" style="left:110px;top:1639px;width:430px">The ecosystem is designed around clear separation of responsibilities. Governance activities belong at the framework layer. Operational workflows, where available, belong on a separate operating platform designed for process execution and recordkeeping. Assets and project execution, where applicable, belong at the project level through ring-fenced structures created for specific initiatives. This separation is intended to reduce ambiguity and help stakeholders understand who is responsible for what.</p>
</section>

<!-- Ecosystem -->
<section>
  <div class="abs" style="left:448px;top:1908px;width:752px;height:698px;background:var(--black)"></div>
  <div class="photo" style="left:0;top:1908px;width:448px;height:698px;background:linear-gradient(180deg,#c7ccd1 0%,#8a98a6 35%,#3f4d5c 70%,#6b6f72 100%)" role="img" aria-label="Twin glass towers joined by a sky bridge above a waterfront"></div>
  <div class="photo" style="left:620px;top:1459px;width:580px;height:529px;background:linear-gradient(180deg,#b5a6b8 0%,#d7b9a8 30%,#9b8473 60%,#c8b59c 100%)" role="img" aria-label="Terraced beachfront residential building at sunset"></div>
  <h2 class="section-title abs" style="left:499px;top:2062px;color:var(--white);width:340px">How the Ecosystem Works</h2>
  <a class="btn" style="left:956px;top:2112px;width:151px;height:31px">Learn the Framework</a>
  <p class="abs" style="left:499px;top:2168px;font-size:10.5px;color:var(--white)">At a high level, the ecosystem can be understood as three layers:</p>
  <div class="eco-card" style="left:385px"><h3>Governance</h3><p>defines standards, explains role boundaries, and publishes framework information.</p></div>
  <div class="eco-card" style="left:631px"><h3>Operations</h3><p>Manages workflow processes such as documentation steps and record-anchored audit events through a separate platform.</p></div>
  <div class="eco-card" style="left:877px"><h3>Project execution</h3><p>Occurs at the project level through dedicated structures that hold responsibilities and assets where applicable.</p></div>
  <p class="abs" style="left:499px;top:2490px;width:600px;font-size:10.5px;line-height:1.6;color:var(--white)">This website focuses on the governance layer and provides links to learn about structural concepts such as role separation, escrow and milestone framing, and recordkeeping terminology.</p>
</section>

<!-- Escrow -->
<section>
  <h2 class="section-title abs" style="left:110px;top:2843px;width:460px">Independent Escrow and Milestone Oversight</h2>
  <p class="body-text abs" style="left:110px;top:2946px;width:460px">Some initiatives use independent escrow arrangements to coordinate staged releases linked to milestone completion. Escrow can support execution discipline by requiring defined evidence before releases occur. Escrow does not guarantee outcomes, timelines, or success, and it is not administered by this website operator. This site describes the concept for clarity and transparency.</p>
  <div class="abs" style="left:758px;top:2900px;width:305px;height:256px;border:2px solid var(--violet);border-left:none;border-top:none"></div>
  <div class="abs" style="left:1040px;top:2835px;width:23px;height:2px;background:var(--violet)"></div>
  <div class="photo" style="left:646px;top:2718px;width:389px;height:411px;background:linear-gradient(160deg,#6f9ac6,#2f4f73 45%,#c9bba6 80%,#a08f7a)" role="img" aria-label="Residential tower beside a tall glass office tower"></div>
  <div class="photo" style="left:813px;top:2995px;width:272px;height:174px;background:linear-gradient(160deg,#c9d3dd,#5b7b99 50%,#3a5873);border:4px solid var(--white);box-shadow:0 10px 24px rgba(0,0,0,.18)" role="img" aria-label="Aerial view of glass towers above the clouds"></div>
</section>

<!-- Operational workflows -->
<section>
  <div class="abs" style="left:0;top:3263px;width:1200px;height:235px;background:var(--mist)"></div>
  <h2 class="section-title abs" style="left:161px;top:3335px;width:380px">Where Operational Workflows Happen</h2>
  <p class="body-text abs" style="left:604px;top:3316px;width:455px">Operational workflows, including any onboarding or workflow participation where permitted, occur on a separate operating platform under separate terms and policies. If you need operational access, use the Halvemark page on this site to navigate externally. This website does not host those workflows.</p>
  <a class="btn" style="left:604px;top:3410px;width:161px;height:31px">Continue to Halvemark</a>
</section>

<!-- Image band -->
<section>
  <div class="photo" style="left:0;top:3498px;width:281px;height:475px;background:linear-gradient(170deg,#2f7a94,#5f9fae 45%,#c8b79a 80%,#9aa79c)" role="img" aria-label="Aerial view of a coastline with marinas"></div>
  <div class="photo" style="left:281px;top:3498px;width:240px;height:475px;background:linear-gradient(90deg,#efe3cf,#e6d3b4 45%,#55606b 60%,#33404c)" role="img" aria-label="Close view of a pale tower facade beside a glass tower"></div>
  <div class="photo" style="left:521px;top:3498px;width:679px;height:475px;background:linear-gradient(180deg,#b8b0a4 0%,#c9a887 30%,#4b8a8c 65%,#c9b08d 100%)" role="img" aria-label="Aerial city skyline along a turquoise waterfront"></div>
</section>

<!-- Contact -->
<section>
  <h2 class="section-title abs" style="left:0;top:4032px;width:1200px;text-align:center">Contact and Inquiries</h2>
  <p class="body-text abs" style="left:280px;top:4093px;width:640px;text-align:center">If you have questions about governance framework concepts, role boundaries, or information published on this website, you can contact the team using the Contact page. Do not submit sensitive personal data through public forms.</p>
  <a class="btn" style="left:525px;top:4151px;width:150px;height:33px">Contact the Team</a>
</section>

<!-- Footer -->
<footer class="footer">
  <div class="brand" style="left:95px;top:188px;font-size:24px"><span class="dot" style="width:34px;height:34px"></span>THE COPPER LANTERN</div>
  <div class="f-col" style="left:448px">
    <h4>Company</h4>
    <ul><li>Framework</li><li>Projects</li><li>Halvemark</li><li>Insights</li><li>Company</li><li>Contact</li><li>Glossary</li></ul>
  </div>
  <div class="f-col" style="left:640px">
    <h4>Legal</h4>
    <ul><li>Legal</li><li>Terms of Use</li><li>Privacy Policy</li><li>Cookie Policy</li><li>Disclaimer &amp; Risk Notices</li><li>Acceptable Use Policy</li><li>Accessibility Statement</li></ul>
  </div>
  <div class="f-col" style="left:857px;width:270px">
    <h4>This site is informational.</h4>
    <p style="font-size:11px;line-height:1.55;color:#d6d6d6">This website is provided for general informational purposes only. Nothing on this site is an offer, solicitation, or professional advice.</p>
  </div>
  <div class="f-rule"></div>
  <p class="copy">© 2026 The Copper Lantern. All rights reserved.</p>
</footer>

</body>
</html>
```